Victorian Era general store concept

I want to design a Victorian era general store themed web site. I Have existing advertisements from the Harrow Bay Courier from the 1850's that display the Tindle and Corrow brand. I would like to create a logo with that and if the designer can add any anything to it that would enhance the look yet retain its classic Victorian appear that would be great. I will upload the Harrow bay courier publication. Look for Tindle and Corrow ads on there. I would like the design to be simplistic yet classic. Nothing to busy. I would like to add the phrase "A harrow bay orginal" "Est. 1851"
https://www.oldpress-archive.example/library/papers/paper_detail.aspx?t=29
Updates

I am going to upload another file that is very clear. Tindle and Corrow regular line of packets. Hopefully this will help.

Target Market(s)

Undetermined

Industry/Entity Type

Online Store

Number of Pages Required

1 page

Font styles to use
Other font styles liked:
• What is on the adds.

Colors

Designer to choose colors to be used in the design.

Requirements
Must have
• Harrow Bay orginal and est 1851
• Any "Tindle and Corrow" advertisement from the Harrow Bay Courier with details thereof.
Nice to have
• Some type of ship in the logo would be nice if it fits well.

```html
<!DOCTYPE html>
<html lang="en">
<head>
<meta charset="utf-8">
<title>Tindle and Corrow</title>
<link href="https://fonts.googleapis.com/css2?family=Cinzel:wght@500;600&family=Old+Standard+TT:wght@400;700&family=Open+Sans:wght@400&family=Playfair+Display:wght@700&display=swap" rel="stylesheet">
<style>
  :root {
    --paper: #fcfbf7;
    --ink: #3a3a3a;
    --ink-soft: #555;
    --bar: #454545;
    --rule: #6a6a6a;
    --orange: #f6a04d;
    --slate: #5f5f5f;
  }
  * { box-sizing: border-box; margin: 0; padding: 0; }
  html, body { width: 797px; height: 1200px; overflow: hidden; }
  body { background: var(--paper); color: var(--ink); font-family: "Old Standard TT", serif; position: relative; }
  a { color: inherit; }

  .top-bar { position: absolute; left: 0; top: 0; width: 797px; height: 24px; background: var(--bar); color: #fff; font: 400 8.6px/24px "Open Sans", sans-serif; }
  .top-nav { position: absolute; left: 58px; display: flex; gap: 10px; }
  .top-contact { position: absolute; right: 63px; display: flex; gap: 26px; }
  .top-contact span { display: flex; align-items: center; gap: 5px; }

  .brand { position: absolute; left: 0; top: 40px; width: 797px; text-align: center; }
  .brand-mark { display: block; margin: 0 auto; width: 38px; height: 38px; border-radius: 50%; border: 2px solid var(--ink); }
  .brand-name { font: 600 10.4px "Cinzel", serif; letter-spacing: 2.6px; margin-top: 16px; color: var(--ink); }

  .rule { position: absolute; left: 58px; width: 681px; border-top: 1px solid var(--rule); }
  .tagline { position: absolute; top: 122px; left: 0; width: 797px; text-align: center; font: 600 10.6px "Cinzel", serif; letter-spacing: .3px; color: #222; }

  .hero { position: absolute; left: 58px; top: 178px; width: 449px; height: 386px; color: #fff;
    background:
      radial-gradient(ellipse 55% 40% at 62% 38%, rgba(235,232,226,.55), transparent 70%),
      linear-gradient(180deg, #8d8a86 0%, #a29f9a 30%, #77736f 58%, #4d4a47 80%, #3f3c3a 100%); }
  .hero-title { position: absolute; left: 18px; top: 142px; font: 700 30px/34px "Playfair Display", serif; }
  .hero-sub { position: absolute; left: 21px; top: 256px; font: 700 17px "Old Standard TT", serif; }
  .hero-copy { position: absolute; left: 21px; top: 284px; width: 315px; font-size: 10.4px; line-height: 12.6px; }
  .hero-link { position: absolute; left: 21px; top: 348px; font-size: 10.6px; }

  .categories { position: absolute; left: 526px; top: 183px; width: 213px; }
  .categories h2 { font: 700 13.8px "Old Standard TT", serif; margin-left: 5px; letter-spacing: .2px; }
  .search { margin-top: 9px; height: 28px; border: 1px solid var(--rule); display: flex; align-items: center; justify-content: space-between; padding: 0 14px 0 20px; font-size: 8px; color: #aaa; }
  .cat-list { position: relative; margin-top: 12px; height: 316px; overflow: hidden; list-style: none; }
  .cat-list .group { font: 700 9.6px "Old Standard TT", serif; margin-left: 4px; text-transform: uppercase; line-height: 14px; }
  .cat-list .item { font-size: 11.2px; line-height: 17.4px; margin-left: 17px; color: var(--ink-soft); }
  .cat-list .gap { height: 9px; }
  .scroll-track { position: absolute; left: 727px; top: 250px; width: 3px; height: 304px; background: #e6e6e6; }
  .scroll-thumb { width: 3px; height: 98px; background: #777; }

  .story { position: absolute; top: 582px; width: 216px; }
  .story-rule { border-top: 1px solid var(--rule); border-bottom: 1px solid var(--rule); height: 3px; }
  .story h3 { margin-top: 5px; font: 700 29px/35px "Playfair Display", serif; color: var(--ink); height: 83px; }
  .story-photo { position: relative; height: 154px; overflow: hidden; }
  .ribbon { position: absolute; left: -34px; top: 20px; width: 170px; height: 24px; transform: rotate(-35deg); color: #fff; font: 700 13px/24px "Old Standard TT", serif; text-align: center; letter-spacing: .5px; }
  .ribbon.best { background: var(--orange); }
  .ribbon.new { background: var(--slate); }
  .story p { margin-top: 20px; font-size: 10.6px; line-height: 12.5px; text-align: justify; hyphens: auto; color: #444; }
  .drop { float: left; font-size: 34px; line-height: 25px; margin-right: 1px; }
  .story .more { display: block; margin-top: 12px; font-size: 11.2px; }

  .loading { position: absolute; top: 1129px; left: 0; width: 797px; text-align: center; font-size: 8.6px; display: flex; justify-content: center; gap: 5px; align-items: center; }
  .footer-rule { position: absolute; left: 66px; top: 1156px; width: 664px; border-top: 2px solid #222; }
  .footer { position: absolute; top: 1173px; left: 0; width: 797px; text-align: center; font: 400 8px "Open Sans", sans-serif; }
</style>
</head>
<body>
  <header class="top-bar">
    <nav class="top-nav"><span>Products</span><span>Advertisments</span><span>About Us</span></nav>
    <div class="top-contact">
      <span><svg width="9" height="7" viewBox="0 0 9 7"><rect width="9" height="7" rx="1" fill="#fff"/><path d="M0 0.5 4.5 4 9 0.5" stroke="#454545" fill="none"/></svg>info@tindleandcorrow.example</span>
      <span><svg width="8" height="8" viewBox="0 0 8 8"><path d="M1 0.5 2.8 0.5 3.4 2.4 2.4 3.2Q3.4 4.8 4.8 5.6L5.6 4.6 7.5 5.2 7.5 7Q3.8 7.4 1.2 4.4 0.4 2.6 1 0.5Z" fill="#fff"/></svg>(02) 555 0148</span>
    </div>
  </header>

  <div class="brand">
    <span class="brand-mark"></span>
    <div class="brand-name">TINDLE &amp; CORROW</div>
  </div>
  <div class="rule" style="top:110px"></div>
  <div class="tagline">A HARROW BAY ORIGINAL &nbsp;•&nbsp; EST. 1851</div>
  <div class="rule" style="top:146px"></div>
  <div class="rule" style="top:149px"></div>

  <section class="hero" role="img" aria-label="Sepia photograph of a passenger steamship at sea">
    <h1 class="hero-title">SAN FRANSICO<br>HARROW AND<br>BAY</h1>
    <h2 class="hero-sub">First Class Vessels:</h2>
    <p class="hero-copy">Lorem ipsum dolor sit amet, consectetur adipisicing elit, sed do eiusmod tempor incididunt ut labore et dolore magna aliqua. Ut enim ad minim veniam, quis nostrud exercitation ullamco laboris nisi ut aliquip ex ea commodo consequat.</p>
    <a class="hero-link" href="#">Read More »</a>
  </section>

  <aside class="categories">
    <h2>PRODUCT CATEGORIES</h2>
    <div class="search">Enter your keyword here
      <svg width="11" height="11" viewBox="0 0 11 11"><circle cx="4.5" cy="4.5" r="3.5" stroke="#333" stroke-width="1.6" fill="none"/><path d="M7 7 10 10" stroke="#333" stroke-width="1.8"/></svg>
    </div>
    <ul class="cat-list">
      <li class="group">Ships</li>
      <li class="item">Consectetur</li><li class="item">Adipisicing</li><li class="item">Incididun</li><li class="item">Nostrud</li><li class="item">Exercitation</li><li class="item">Ullamco</li><li class="item">Laboris</li><li class="item">Commodo</li><li class="item">reprehenderit in</li><li class="item">voluptate velit</li><li class="item">esse cillum</li>
      <li class="gap"></li>
      <li class="group">Vessels</li>
      <li class="item">Consectetur</li><li class="item">Adipisicing</li><li class="item">Incididun</li><li class="item">Nostrud</li><li class="item">Exercitation</li>
    </ul>
  </aside>
  <div class="scroll-track"><div class="scroll-thumb"></div></div>

  <article class="story" style="left:57px">
    <div class="story-rule"></div>
    <h3>OCEAN STEAM<br>SHIPS</h3>
    <div class="story-photo" role="img" aria-label="Photograph of a passenger ferry from above" style="background:radial-gradient(ellipse 60% 35% at 60% 55%,#cfcac3,transparent 70%),linear-gradient(160deg,#6b6661,#4a4541 60%,#3b3734)"><div class="ribbon best">BEST SELLER</div></div>
    <p><span class="drop">L</span>orem ipsum dolor sit amet, consectetur adipisicing elit, sed do eiusmod tempor incididunt ut labore et dolore magna aliqua. Ut enim ad minim veniam, quis nostrud exercitation ullamco laboris nisi ut aliquip ex ea commodo consequat. Duis aute irure dolor in reprehenderit in voluptate velit esse cillum dolore eu fugiat nulla pariatur. Excepteur sint occaecat cupidatat non proident, sunt in culpa qui officia deserunt mollit anim id est laborum. Sed ut perspiciatis unde omnis iste natus error sit voluptatem accusantium doloremque laudantium, totam rem aperiam, eaque ipsa quae ab i proident, sunt in culpa qui officia deserunt mollit anim id est laborum. Sed ut perspiciatis</p>
    <a class="more" href="#">Learn More »</a>
  </article>

  <article class="story" style="left:291px">
    <div class="story-rule"></div>
    <h3>THIS HOUSE<br>IS FOR SALE</h3>
    <div class="story-photo" role="img" aria-label="Photograph of a brick cottage with a garden path" style="background:linear-gradient(180deg,#c9c6c1 0%,#a9a5a0 22%,#6e6963 45%,#5a5550 70%,#48443f 100%)"><div class="ribbon best">BEST SELLER</div></div>
    <p><span class="drop">T</span>orem ipsum dolor sit amet, consectetur adipisicing elit, sed do eiusmod tempor incididunt ut labore et dolore magna aliqua. Ut enim ad minim veniam, quis nostrud exercitation ullamco laboris nisi ut aliquip ex ea commodo consequat. Duis aute irure dolor in reprehenderit in voluptate velit esse cillum dolore eu fugiat nulla pariatur. Excepteur sint occaecat cupidatat non proident, sunt in culpa qui officia deserunt mollit anim id est laborum. Sed ut perspiciatis unde omnis iste natus error sit voluptatem accusantium doloremque laudantium, totam rem aperiam, eaque ipsa quae ab i proident, sunt in culpa qui officia deserunt mollit anim id est laborum. Sed ut perspiciatis</p>
    <a class="more" href="#">Learn More »</a>
  </article>

  <article class="story" style="left:523px">
    <div class="story-rule"></div>
    <h3>VINTAGE<br>BIKE</h3>
    <div class="story-photo" role="img" aria-label="Photograph of a vintage bicycle against a white wall" style="background:linear-gradient(180deg,#efeeeb 0%,#e4e2de 78%,#8f8b86 88%,#6e6a65 100%)"><div class="ribbon new">NEW ARRIVAL</div></div>
    <p><span class="drop">G</span>et psum dolor sit amet, consectetur adipisicing elit, sed do eiusmod tempor incididunt ut labore et dolore magna aliqua. Ut enim ad minim veniam, quis nostrud exercitation ullamco laboris nisi ut aliquip ex ea commodo consequat. Duis aute irure dolor in reprehenderit in voluptate velit esse cillum dolore eu fugiat nulla pariatur. Excepteur sint occaecat cupidatat non proident, sunt in culpa qui officia deserunt mollit anim id est laborum. Sed ut perspiciatis unde omnis iste natus error sit voluptatem accusantium doloremque laudantium, totam rem aperiam, eaque ipsa quae ab i proident, sunt in culpa qui officia deserunt mollit anim id est laborum. Sed ut perspiciatis</p>
    <a class="more" href="#">Learn More »</a>
  </article>

  <div class="loading">Loading more ads please wait
    <svg width="9" height="9" viewBox="0 0 10 10"><path d="M2.2 3A3.4 3.4 0 1 1 1.6 6" stroke="#222" stroke-width="1.4" fill="none"/><path d="M0.6 1 3.4 3.6 0.6 4.4Z" fill="#222"/></svg>
  </div>
  <div class="footer-rule"></div>
  <footer class="footer">Tindle and Corrow 2018. All rights Reserved</footer>
</body>
</html>
```